AGP letterhead

We need a letterhead design for our new company based in Los Angeles called "Amber Gate Pictures". We develop film and television projects. We work with investors, financiers, film production companies, film distribution and sales companies as well as studios. We would like to incorporate our logo (see attached) but make the letterhead simple and elegant. We need to include: logo, company address, phone number and company website.
Updates

Hello designers, Thanks for your submissions. For our letterhead, we are looking for something more simple and elegant. No heavy bars or lines. Make it feel light and clean. Not a lot of ink on the page. Use the logo and contact info but think "clean", "streamlined" and mostly white paper. Looking forward to seeing more... thanks! Amber Gate Pictures team

Target Market(s)

Studio executives, talent agents and agencies, financiers, investors.

Industry/Entity Type

It Company

Requirements
Must have
• Amber Gate Pictures logo (see attached). Logo may be cropped and altered appropriately for elegant letterhead design.
• Please include:
• COMPANY ADDRESS:
• Tolvane Arts Park
• 2850 Delmore Street
• Crest Hall, 2nd Floor
• Manhattan Beach, CA 90266
• COMPANY WEBSITE:
• www.ambergatepicturesco.example
• COMPANY PHONE NUMBER:
• 555-604-2187

```html
<!DOCTYPE html>
<html lang="en">
<head>
<meta charset="utf-8">
<title>Amber Gate Pictures — Letterhead</title>
<link rel="stylesheet" href="https://fonts.googleapis.com/css2?family=Dosis:wght@400;500;600&display=swap">
<style>
  :root {
    --backdrop: #e9eaec;
    --paper: #ffffff;
    --edge-line: #9fb0b8;
    --brand-blue: #1b7fb3;
    --ink: #2a2a2a;
    --ink-soft: #555b60;
  }
  * { box-sizing: border-box; margin: 0; padding: 0; }
  html, body {
    width: 1200px; height: 936px; overflow: hidden;
    background: var(--backdrop);
    font-family: "Dosis", sans-serif;
  }
  .sheet {
    position: absolute;
    left: 297px; top: 38px;
    width: 606px; height: 860px;
    background: var(--paper);
    box-shadow: 0 2px 10px rgba(0,0,0,0.12);
  }
  .sheet__edge {
    position: absolute; right: 14px; top: 40px; bottom: 40px;
    width: 1px;
    background: var(--edge-line);
  }
  .brand {
    position: absolute; left: 58px; top: 58px;
    display: flex; align-items: center; gap: 10px;
  }
  .brand__dot {
    width: 30px; height: 30px; border-radius: 50%;
    background: var(--brand-blue);
  }
  .brand__text { display: flex; flex-direction: column; }
  .brand__name {
    color: var(--brand-blue);
    font-weight: 600; font-size: 17px;
    letter-spacing: 0.06em; text-transform: uppercase;
    line-height: 1.1;
  }
  .brand__tagline {
    color: var(--ink-soft);
    font-weight: 500; font-size: 6.5px;
    letter-spacing: 0.18em; text-transform: uppercase;
    margin-top: 3px;
  }
  .contact {
    position: absolute; left: 370px; bottom: 56px;
    list-style: none;
    color: var(--ink);
    font-size: 11.5px; font-weight: 500;
    line-height: 1.45;
  }
  .contact__item { display: flex; align-items: flex-start; gap: 7px; }
  .contact__icon { width: 9px; height: 9px; margin-top: 4px; flex: none; }
  .contact__icon--blank { visibility: hidden; }
</style>
</head>
<body>
  <main class="sheet">
    <div class="brand">
      <span class="brand__dot"></span>
      <div class="brand__text">
        <span class="brand__name">Amber Gate Pictures</span>
        <span class="brand__tagline">A Media Entertainment Company</span>
      </div>
    </div>

    <ul class="contact">
      <li class="contact__item">
        <svg class="contact__icon" viewBox="0 0 10 10"><path d="M5 0.5a3.3 3.3 0 0 0-3.3 3.3C1.7 6.2 5 9.5 5 9.5s3.3-3.3 3.3-5.7A3.3 3.3 0 0 0 5 .5zm0 4.6a1.3 1.3 0 1 1 0-2.6 1.3 1.3 0 0 1 0 2.6z" fill="#2a2a2a"/></svg>
        <span>Tolvane Arts Park</span>
      </li>
      <li class="contact__item">
        <svg class="contact__icon contact__icon--blank" viewBox="0 0 10 10"></svg>
        <span>2850 Delmore Street</span>
      </li>
      <li class="contact__item">
        <svg class="contact__icon contact__icon--blank" viewBox="0 0 10 10"></svg>
        <span>Crest Hall, 2nd Floor</span>
      </li>
      <li class="contact__item">
        <svg class="contact__icon contact__icon--blank" viewBox="0 0 10 10"></svg>
        <span>Manhattan Beach, CA 90266</span>
      </li>
      <li class="contact__item">
        <svg class="contact__icon" viewBox="0 0 10 10"><circle cx="5" cy="5" r="4.5" fill="#2a2a2a"/><path d="M3.4 2.6l1 1-.5.7c.4.8 1 1.4 1.8 1.8l.7-.5 1 1-.6.8C4.8 7.2 2.8 5.2 2.6 3.2z" fill="#fff"/></svg>
        <span>555-604-2187</span>
      </li>
      <li class="contact__item">
        <svg class="contact__icon" viewBox="0 0 10 10"><rect x="0.5" y="2" width="9" height="6.5" rx="0.8" fill="#2a2a2a"/><path d="M1 2.6l4 3 4-3" stroke="#fff" stroke-width="0.9" fill="none"/></svg>
        <span>jonas@ambergatepicturesco.example</span>
      </li>
      <li class="contact__item">
        <svg class="contact__icon" viewBox="0 0 10 10"><circle cx="5" cy="5" r="4.2" fill="none" stroke="#2a2a2a" stroke-width="1.1"/><ellipse cx="5" cy="5" rx="1.8" ry="4.2" fill="none" stroke="#2a2a2a" stroke-width="0.8"/><path d="M0.8 5h8.4" stroke="#2a2a2a" stroke-width="0.8"/></svg>
        <span>www.ambergatepicturesco.example</span>
      </li>
    </ul>

    <div class="sheet__edge"></div>
  </main>
</body>
</html>
```